Local fast-growing company in the service sector

We are looking for a modern business card design, which should also appear on our letterheads

Target Market(s)

Private and industrial sectors

Contact Information for Business Card

Vorname Name
Kellberger Str. 18
73614 Schorndorf
Tel.: 07146-839214-0
Name@agentur-kvtl.de

Colors
9d9d9d
919191
aaaaaa

Requirements
Must have
• The logo (file) in silver

```html
<!DOCTYPE html>
<html lang="de">
<head>
<meta charset="utf-8">
<title>KVTL Visitenkarte</title>
<link rel="stylesheet" href="https://fonts.googleapis.com/css2?family=Source+Sans+3:wght@400;600&display=swap">
<style>
  :root {
    --backdrop: #575757;
    --card-front: #ffffff;
    --card-back: #141414;
    --pattern-tone: #2a2a2a;
    --silver: #9d9d9d;
    --silver-light: #aaaaaa;
    --text-dark: #3c3c3c;
    --rule: #919191;
  }
  * { margin: 0; padding: 0; box-sizing: border-box; }
  html, body { width: 1200px; height: 900px; overflow: hidden; }
  body {
    background: var(--backdrop);
    font-family: "Source Sans 3", "Myriad Pro", Arial, sans-serif;
    position: relative;
  }
  .card {
    position: absolute;
    top: 306px;
    width: 439px;
    height: 271px;
    border-radius: 12px;
    overflow: hidden;
  }
  .card--front { left: 149px; background: var(--card-front); }
  .card--back { left: 609px; background: var(--card-back); }

  .brand {
    position: absolute;
    right: 23px;
    top: 54px;
    display: flex;
    align-items: center;
    gap: 14px;
  }
  .brand__square {
    width: 44px; height: 44px;
    background: var(--silver);
  }
  .brand__name {
    font-weight: 600;
    font-size: 50px;
    letter-spacing: 1px;
    color: var(--silver);
    line-height: 1;
  }

  .holder {
    position: absolute;
    left: 25px;
    top: 163px;
    width: 391px;
    display: flex;
    align-items: center;
    gap: 14px;
  }
  .holder__name {
    font-size: 16px;
    font-weight: 600;
    color: var(--text-dark);
    letter-spacing: 0.2px;
    white-space: nowrap;
  }
  .holder__rule {
    flex: 1;
    height: 1px;
    background: var(--rule);
    margin-top: -6px;
  }

  .contact {
    position: absolute;
    left: 24px;
    top: 197px;
    list-style: none;
    font-size: 13px;
    line-height: 16.5px;
    color: var(--text-dark);
  }
  .contact__item { display: flex; align-items: center; gap: 5px; white-space: nowrap; }
  .contact__icon { width: 11px; height: 11px; fill: var(--text-dark); flex: none; }

  .address {
    position: absolute;
    right: 23px;
    top: 214px;
    text-align: right;
    font-style: normal;
    font-size: 13px;
    line-height: 17px;
    color: var(--text-dark);
    white-space: nowrap;
  }

  .back-pattern {
    position: absolute; inset: 0;
    background: radial-gradient(circle at 60% 50%, var(--pattern-tone), var(--card-back) 75%);
  }
  .back-brand {
    position: absolute;
    left: 323px;
    top: 145px;
    font-size: 14px;
    font-weight: 600;
    color: var(--silver-light);
    letter-spacing: 0.5px;
  }
</style>
</head>
<body>
  <section class="card card--front" aria-label="Visitenkarte Vorderseite">
    <div class="brand">
      <span class="brand__square"></span>
      <span class="brand__name">KVTL</span>
    </div>

    <div class="holder">
      <span class="holder__name">VORNAME NAME</span>
      <span class="holder__rule"></span>
    </div>

    <ul class="contact">
      <li class="contact__item">
        <svg class="contact__icon" viewBox="0 0 24 24"><path d="M6.6 10.8c1.4 2.8 3.8 5.1 6.6 6.6l2.2-2.2c.3-.3.7-.4 1-.2 1.1.4 2.3.6 3.6.6.6 0 1 .4 1 1V20c0 .6-.4 1-1 1C10.6 21 3 13.4 3 4c0-.6.4-1 1-1h3.5c.6 0 1 .4 1 1 0 1.3.2 2.5.6 3.6.1.3 0 .7-.2 1l-2.3 2.2z"/></svg>
        07146-839214-0
      </li>
      <li class="contact__item">
        <svg class="contact__icon" viewBox="0 0 24 24"><path d="M2 5h20v14H2z M2 5l10 7 10-7" stroke="#fff" stroke-width="1.5"/></svg>
        Name@agentur-kvtl.de
      </li>
      <li class="contact__item">
        <svg class="contact__icon" viewBox="0 0 24 24"><circle cx="12" cy="12" r="10"/><path d="M2 12h20M12 2c3 3 3 17 0 20M12 2c-3 3-3 17 0 20" stroke="#fff" stroke-width="1.5" fill="none"/></svg>
        www.agentur-kvtl.de
      </li>
    </ul>

    <address class="address">
      Kellberger Str. 18<br>
      73614 Schorndorf
    </address>
  </section>

  <section class="card card--back" aria-label="Visitenkarte Rückseite">
    <div class="back-pattern" role="img" aria-label="Dunkler Hintergrund mit wiederholtem Markenmuster"></div>
    <span class="back-brand">KVTL</span>
  </section>
</body>
</html>
```